Business Cards Design for the electrical wholesaler: clean bold dynamic :)

We need a business card design that would follow our latest brand guidelines. As an electrical wholesaler we want to bring a fresh look and feel into the industry. The design should be clean bold and dynamic. It should come alive with the renewed energy of our green colour. Our grey colour should keep things balanced and complement the notion of maturity and responsibility. We employ Lato as a corporate font however are not bound by this font and we’re open to interpretation here.

Target Market(s)

Electrical contractors

Industry/Entity Type

Business

Contact Information for Business Card

Logo
Name & Surname: Halyna Dorosh
Job Title: Director of Marketing
Email: halya.dorosh@quillmail.example
Cell phone: XXX.XXX.XXXX
Address: 20517 - 87 Ave. Edmonton, AB, Canada. T6K 4N8
Business Phone: 780.555.0184
Website: www.brovix.example

Font styles to use
Other font styles liked:
• Lato

Requirements
Must have
• Logo & website
Nice to have
• Brand elements - some of them you may find in the attached Brand Guidelines (e.g. three lines on the background signifying "W")

```html
<!DOCTYPE html>
<html lang="en">
<head>
<meta charset="utf-8">
<title>Brovix Business Card</title>
<link href="https://fonts.googleapis.com/css2?family=Lato:wght@400;700&display=swap" rel="stylesheet">
<style>
  :root {
    --stage: #333333;
    --card-white: #ffffff;
    --brand-green: #8cc63f;
    --brand-grey: #4d4d4f;
    --text-dark: #2b2b2b;
    --rule: #6d6d6d;
  }
  * { margin: 0; padding: 0; box-sizing: border-box; }
  html, body { width: 1200px; height: 900px; overflow: hidden; }
  body {
    background: var(--stage);
    font-family: "Lato", sans-serif;
    position: relative;
  }
  .card {
    position: absolute;
    top: 306px;
    width: 439px;
    height: 271px;
    border-radius: 10px;
    overflow: hidden;
  }
  .card-front { left: 149px; background: var(--card-white); }
  .card-back { left: 608px; background: var(--brand-green); }

  .brand-lockup {
    position: absolute;
    left: 40px;
    top: 120px;
    width: 170px;
    text-align: center;
  }
  .brand-name {
    display: inline-flex;
    align-items: center;
    gap: 8px;
    font-size: 44px;
    font-weight: 400;
    color: var(--brand-grey);
    line-height: 1;
  }
  .brand-dot {
    width: 14px; height: 14px;
    border-radius: 50%;
    background: var(--brand-green);
  }
  .brand-tagline {
    margin-top: 18px;
    font-size: 7.5px;
    letter-spacing: 1.4px;
    color: var(--brand-grey);
    white-space: nowrap;
  }

  .divider {
    position: absolute;
    left: 219px;
    top: 66px;
    width: 1px;
    height: 138px;
    background: var(--rule);
  }

  .contact-block {
    position: absolute;
    left: 241px;
    top: 66px;
    color: var(--text-dark);
  }
  .person-name {
    font-size: 16px;
    font-weight: 400;
    letter-spacing: 0.4px;
    text-transform: uppercase;
    color: var(--brand-grey);
    line-height: 18px;
  }
  .person-name .surname { color: var(--brand-green); }
  .person-title { font-size: 12px; line-height: 16px; margin-bottom: 6px; }
  .contact-list { list-style: none; }
  .contact-list li {
    display: flex;
    align-items: center;
    gap: 6px;
    font-size: 12px;
    line-height: 16px;
  }
  .contact-list svg { width: 10px; height: 10px; flex: none; fill: var(--brand-green); }
  .address { margin-top: 6px; font-size: 12px; line-height: 16px; }

  .back-pattern {
    position: absolute;
    inset: 0;
    background: linear-gradient(135deg, #93ca4a, #86c13a);
  }
  .back-brand {
    position: absolute;
    inset: 0;
    display: flex;
    align-items: center;
    justify-content: center;
    font-size: 28px;
    font-weight: 700;
    color: var(--card-white);
  }
</style>
</head>
<body>

  <section class="card card-front" aria-label="Business card front">
    <div class="brand-lockup">
      <div class="brand-name"><span>brovix</span><span class="brand-dot"></span></div>
      <div class="brand-tagline">ELECTRICAL WHOLESALERS</div>
    </div>

    <div class="divider"></div>

    <div class="contact-block">
      <p class="person-name">Halyna <span class="surname">Dorosh</span></p>
      <p class="person-title">Director of Marketing</p>
      <ul class="contact-list">
        <li>
          <svg viewBox="0 0 10 10" aria-hidden="true"><path d="M1 3.2C1 2 2.5 1.2 5 1.2S9 2 9 3.2L7.4 3.8 6.8 2.8H3.2L2.6 3.8zM2.4 4.6h5.2L8.6 8.8H1.4z"/></svg>
          <span>780.555.0184</span>
        </li>
        <li>
          <svg viewBox="0 0 10 10" aria-hidden="true"><path d="M3 0.5h4a0.8 0.8 0 0 1 0.8 0.8v7.4a0.8 0.8 0 0 1-0.8 0.8H3a0.8 0.8 0 0 1-0.8-0.8V1.3A0.8 0.8 0 0 1 3 0.5zM3.2 1.6v6h3.6v-6z"/></svg>
          <span>780.555.0239</span>
        </li>
        <li>
          <svg viewBox="0 0 10 10" aria-hidden="true"><path d="M0.8 2h8.4v6H0.8zM1.6 2.6L5 5.4 8.4 2.6"/><path d="M1.4 2.7L5 5.6l3.6-2.9" fill="none" stroke="#fff" stroke-width="0.8"/></svg>
          <span>halya.dorosh@quillmail.example</span>
        </li>
        <li>
          <svg viewBox="0 0 10 10" aria-hidden="true"><circle cx="5" cy="5" r="4.3"/><path d="M0.8 5h8.4M5 0.8c-2 2.4-2 6 0 8.4M5 0.8c2 2.4 2 6 0 8.4" fill="none" stroke="#fff" stroke-width="0.6"/></svg>
          <span>www.brovix.example</span>
        </li>
      </ul>
      <p class="address">20517 - 87 Ave. Edmonton,<br>AB, Canada. T6K 4N8</p>
    </div>
  </section>

  <section class="card card-back" aria-label="Business card back">
    <div class="back-pattern" role="img" aria-label="Repeating faint brand pattern in light green tones"></div>
    <div class="back-brand">brovix</div>
  </section>

</body>
</html>
```